Business Card for a New Zealand IT Startup

I need a business card for VELTA Holdings. We are a young startup based in New Zealand working in internet marketing and web development. The design should have some element connected to New Zealand, such as wave, koru or silver fern, just don't use a kiwi bird.

```html
<!DOCTYPE html>
<html lang="en">
<head>
<meta charset="utf-8">
<title>VELTA Holdings – Business Card</title>
<link rel="stylesheet" href="https://fonts.googleapis.com/css2?family=Montserrat:wght@500;600;700&family=Open+Sans:wght@400;600&display=swap">
<style>
  :root {
    --bg: #9a9a9a;
    --blue: #1a78c2;
    --blue-deep: #1167b1;
    --orange: #ee5a2a;
    --white: #ffffff;
    --ink: #555b63;
  }
  * { box-sizing: border-box; margin: 0; padding: 0; }
  html, body { width: 1200px; height: 930px; overflow: hidden; }
  body {
    background: radial-gradient(ellipse at 50% 45%, #c4c4c4 0%, var(--bg) 75%);
    position: relative;
    font-family: "Open Sans", sans-serif;
  }
  .card {
    position: absolute;
    width: 560px;
    height: 320px;
    border-radius: 26px;
    overflow: hidden;
    box-shadow: 0 10px 24px rgba(0,0,0,0.28);
  }
  /* Front */
  .card-front {
    left: 90px; top: 110px;
    background: linear-gradient(135deg, #2585cd 0%, var(--blue-deep) 100%);
  }
  .fern-decoration {
    position: absolute;
    left: 70px; top: 20px;
    width: 300px; height: 300px;
    border-radius: 50%;
    background: radial-gradient(circle, rgba(255,255,255,0.12) 0%, rgba(255,255,255,0) 70%);
  }
  .front-brand {
    position: absolute;
    left: 0; right: 0; top: 118px;
    text-align: center;
    font-family: "Montserrat", sans-serif;
    font-weight: 700;
    color: var(--white);
    font-size: 46px;
    letter-spacing: 3px;
    line-height: 1;
  }
  .front-brand .brand-sub {
    display: block;
    font-size: 18px;
    letter-spacing: 14px;
    margin-top: 12px;
  }
  /* Back */
  .card-back {
    left: 560px; top: 500px;
    background: var(--white);
  }
  .back-wave { position: absolute; inset: 0; }
  .back-brand {
    position: absolute;
    left: 36px; top: 172px;
    font-family: "Montserrat", sans-serif;
    font-weight: 700;
    color: var(--blue);
    font-size: 36px;
    letter-spacing: 2px;
    line-height: 1;
  }
  .back-brand .brand-sub {
    display: block;
    font-size: 14px;
    letter-spacing: 10px;
    margin-top: 8px;
  }
  .person {
    position: absolute;
    right: 40px; top: 146px;
    text-align: right;
  }
  .person-name {
    font-family: "Montserrat", sans-serif;
    font-weight: 600;
    font-size: 22px;
    color: var(--blue);
    letter-spacing: 0.5px;
  }
  .person-title {
    font-size: 13px;
    color: var(--orange);
  }
  .rule {
    position: absolute;
    height: 1.5px;
    background: var(--blue);
  }
  .rule-top { right: 40px; top: 204px; width: 220px; }
  .rule-bottom { left: 36px; top: 240px; width: 200px; }
  .address {
    position: absolute;
    right: 40px; top: 214px;
    text-align: right;
    font-size: 12.5px;
    line-height: 1.5;
    color: var(--ink);
  }
  .contacts {
    position: absolute;
    left: 36px; top: 248px;
    list-style: none;
    font-size: 12.5px;
    line-height: 1.45;
    color: var(--ink);
  }
  .contacts li { display: flex; align-items: center; gap: 7px; }
  .contacts svg { width: 10px; height: 10px; fill: var(--blue); flex: none; }
  .contacts .accent { color: var(--orange); }
</style>
</head>
<body>

<section class="card card-front" aria-label="Business card front">
  <div class="fern-decoration" role="img" aria-label="Faint silver fern frond decoration"></div>
  <div class="front-brand">VELTA<span class="brand-sub">HOLDINGS</span></div>
</section>

<section class="card card-back" aria-label="Business card back">
  <svg class="back-wave" viewBox="0 0 560 320" preserveAspectRatio="none" aria-hidden="true">
    <path d="M0,0 H560 V34 C480,100 380,112 280,116 C170,120 70,112 0,132 Z" fill="#1a78c2"/>
    <path d="M560,44 C480,110 380,122 280,126 C170,130 70,122 0,142" fill="none" stroke="#ee5a2a" stroke-width="8"/>
    <path d="M0,160 C40,144 100,136 180,132" fill="none" stroke="#1a78c2" stroke-width="7"/>
  </svg>

  <div class="back-brand">VELTA<span class="brand-sub">HOLDINGS</span></div>

  <div class="person">
    <p class="person-name">DANIEL REEVE</p>
    <p class="person-title">Director</p>
  </div>
  <div class="rule rule-top"></div>
  <p class="address">52 Harbour Lane,<br>Christchurch, NZ, 8013</p>

  <div class="rule rule-bottom"></div>
  <ul class="contacts">
    <li><svg viewBox="0 0 10 10"><path d="M2 0 L4 2 L3 3.5 Q4.5 6 6.5 7 L8 6 L10 8 L8.5 10 Q3 9 0 2 Z"/></svg><span>(514) 555-0142</span></li>
    <li><svg viewBox="0 0 10 10"><path d="M0 2 H10 V8 H0 Z M1 3 V7 H9 V3 L5 5.5 Z" fill-rule="evenodd"/></svg><span>info@veltaholdings.com</span></li>
    <li><svg viewBox="0 0 10 10"><circle cx="5" cy="5" r="5"/></svg><span>www.<span class="accent">veltaholdings</span>.com</span></li>
  </ul>
</section>

</body>
</html>
```